K3 Innovation Wheel and Workflow

Update existing wheel graphic (7 stages) and workflow methodology (56 element grid)

1. Need a new modern icon wheel
2. Reference job titles with the 7 stages somehow (the analyst, the planner, etc.)
3. Center of wheel? = K3 INNOVATION WHEEL (Trademark and Copyright marks)
4. Official name of the model = The K3 Marketing System is a next-gen INNOVATION and GROWTH model with a workflow process. (tm/copyright)
5 We like the Quellbrook color palette but are flexible to leave color to the designer

Logo Text

K3? K3 Innovation Wheel?

Requirements
Must have
• INTERPRET , the Analyst; business intelligence (Bi)

INNOVATE , the Planner; roadmap and lifecycle management

IDENTIFY , the Story teller; individuate innermost value

INVEST , the Catalyst ; below 0 total-cost-of-ownership

IMPLEMENT , the Enabler; agile systems, platforms and channels

INFLUENCE , the Customer Owner; ignite, inspire, incite and promote

INSPECT , the auditor; cross functional measurement, Bi scrums

```html
<!DOCTYPE html>
<html lang="en">
<head>
<meta charset="utf-8">
<title>K3 Innovation Wheel</title>
<link rel="stylesheet" href="https://fonts.googleapis.com/css2?family=Oswald:wght@700&family=Montserrat:wght@600;800;900&family=Mulish:wght@400&display=swap">
<style>
  :root {
    --page-bg: #e7e9ec;
    --sheet: #ffffff;
    --brand-blue: #0b6fa8;
    --k3-blue: #0a8ad6;
    --ink: #2b2b2b;
    --ink-soft: #3c3c3c;
    --ring-grey: #d9d9d9;
    --yellow: #f6b400;
    --yellow-dark: #cf8f00;
    --red: #ef4c1e;
    --red-dark: #b8300f;
    --green: #7dba0f;
    --green-dark: #4f8a07;
    --grey: #5e5e5e;
    --grey-dark: #3b3b3b;
    --blue: #1b9be4;
    --blue-dark: #0b6cb2;
  }
  html, body {
    margin: 0;
    width: 1200px;
    height: 900px;
    overflow: hidden;
    background: var(--page-bg);
  }
  .sheet {
    position: absolute;
    left: 113px;
    top: 10px;
    width: 973px;
    height: 879px;
    background: var(--sheet);
    box-shadow: 0 4px 18px rgba(0,0,0,.15);
  }
  .sheet svg { display: block; }
  .header-band { fill: var(--brand-blue); }
  .rule { stroke: #fff; stroke-width: 3; }
  .kicker {
    font-family: "Montserrat", sans-serif;
    font-weight: 600;
    font-size: 36px;
    fill: #fff;
  }
  .headline {
    font-family: "Oswald", sans-serif;
    font-weight: 700;
    font-size: 170px;
    fill: #fff;
  }
  .hub-mark {
    font-family: "Montserrat", sans-serif;
    font-weight: 900;
    font-size: 230px;
    fill: var(--k3-blue);
    letter-spacing: -8px;
  }
  .hub-label {
    font-family: "Montserrat", sans-serif;
    font-weight: 800;
    font-size: 52px;
    fill: var(--ink);
  }
  .stage-title {
    font-family: "Montserrat", sans-serif;
    font-weight: 800;
    font-size: 34px;
    fill: var(--ink);
  }
  .stage-text {
    font-family: "Mulish", sans-serif;
    font-weight: 400;
    font-size: 24px;
    fill: var(--ink-soft);
  }
  .icon { fill: none; stroke: var(--ink); stroke-width: 2.6; stroke-linecap: round; stroke-linejoin: round; }
  .icon-fill { fill: var(--ink); }
</style>
</head>
<body>
<div class="sheet">
<svg width="973" height="879" viewBox="0 0 1456 1316" xmlns="http://www.w3.org/2000/svg">
  <defs>
    <radialGradient id="hubFace" cx="45%" cy="35%" r="70%">
      <stop offset="0" stop-color="#ffffff"/>
      <stop offset="1" stop-color="#e6e6e6"/>
    </radialGradient>
    <linearGradient id="ringYellow" x1="1" y1="0" x2="0" y2="1"><stop offset=".45" stop-color="var(--yellow)"/><stop offset=".55" stop-color="var(--yellow-dark)"/></linearGradient>
    <linearGradient id="ringRed" x1="1" y1="0" x2="0" y2="1"><stop offset=".45" stop-color="var(--red)"/><stop offset=".55" stop-color="var(--red-dark)"/></linearGradient>
    <linearGradient id="ringGreen" x1="1" y1="0" x2="0" y2="1"><stop offset=".45" stop-color="var(--green)"/><stop offset=".55" stop-color="var(--green-dark)"/></linearGradient>
    <linearGradient id="ringGrey" x1="1" y1="0" x2="0" y2="1"><stop offset=".45" stop-color="var(--grey)"/><stop offset=".55" stop-color="var(--grey-dark)"/></linearGradient>
    <linearGradient id="ringBlue" x1="1" y1="0" x2="0" y2="1"><stop offset=".45" stop-color="var(--blue)"/><stop offset=".55" stop-color="var(--blue-dark)"/></linearGradient>
  </defs>

  <!-- header -->
  <g class="header">
    <rect class="header-band" x="0" y="0" width="1456" height="295"/>
    <rect class="header-band" x="0" y="302" width="1456" height="6"/>
    <text class="kicker" x="41" y="71">THE K3 MARKETING SYSTEM IS A NEXT-GEN</text>
    <line class="rule" x1="826" y1="44" x2="1413" y2="44"/>
    <text class="headline" x="41" y="209" textLength="1372" lengthAdjust="spacingAndGlyphs">INNOVATION AND GROWTH</text>
    <line class="rule" x1="41" y1="262" x2="708" y2="262"/>
    <text class="kicker" x="1415" y="264" text-anchor="end">MODEL WITH A WORKFLOW PROCESS</text>
  </g>

  <!-- wheel hub -->
  <g class="wheel">
    <circle cx="728" cy="637" r="255" fill="none" stroke="#d0d0d0" stroke-width="3" stroke-dasharray="14 10"/>
    <path d="M 483 707 A 255 255 0 0 0 973 707" fill="none" stroke="var(--ring-grey)" stroke-width="4"/>
    <circle cx="728" cy="637" r="212" fill="#dcdcdc"/>
    <circle cx="728" cy="637" r="197" fill="url(#hubFace)"/>
    <text class="hub-mark" x="728" y="669" text-anchor="middle">K3</text>
    <text class="hub-label" x="728" y="722" text-anchor="middle">INNOVATION</text>
    <text class="hub-label" x="728" y="774" text-anchor="middle">PROCESS</text>

    <g class="ring-dots">
      <circle cx="484" cy="577" r="11" fill="#fff" stroke="var(--yellow)" stroke-width="3"/><circle cx="484" cy="577" r="6" fill="var(--yellow)"/>
      <circle cx="977" cy="577" r="11" fill="#fff" stroke="var(--red)" stroke-width="3"/><circle cx="977" cy="577" r="6" fill="var(--red)"/>
      <circle cx="501" cy="747" r="11" fill="#fff" stroke="var(--green)" stroke-width="3"/><circle cx="501" cy="747" r="6" fill="var(--green)"/>
      <circle cx="958" cy="747" r="11" fill="#fff" stroke="var(--green)" stroke-width="3"/><circle cx="958" cy="747" r="6" fill="var(--green)"/>
      <circle cx="600" cy="857" r="11" fill="#fff" stroke="var(--grey)" stroke-width="3"/><circle cx="600" cy="857" r="6" fill="var(--grey)"/>
      <circle cx="859" cy="857" r="11" fill="#fff" stroke="var(--yellow)" stroke-width="3"/><circle cx="859" cy="857" r="6" fill="var(--yellow)"/>
      <circle cx="728" cy="892" r="11" fill="#fff" stroke="var(--blue)" stroke-width="3"/><circle cx="728" cy="892" r="6" fill="var(--blue)"/>
    </g>
  </g>

  <!-- stage: inspect -->
  <g class="stage stage-inspect" transform="translate(354 576)">
    <circle r="95" fill="none" stroke="var(--yellow)" stroke-width="2.5" stroke-dasharray="8 6"/>
    <circle r="82" fill="url(#ringYellow)"/>
    <circle r="47" fill="#fff"/>
    <path class="icon" d="M-32 0 Q0 -28 32 0 Q0 28 -32 0Z"/>
    <circle class="icon" r="11"/>
  </g>
  <text class="stage-title" x="234" y="534" text-anchor="end">INSPECT</text>
  <text class="stage-text" text-anchor="end"><tspan x="234" y="571">The Auditor;</tspan><tspan x="234" y="601">cross functional</tspan><tspan x="234" y="631">performance</tspan></text>

  <!-- stage: interpret -->
  <g class="stage stage-interpret" transform="translate(1105 576)">
    <circle r="95" fill="none" stroke="var(--red)" stroke-width="2.5" stroke-dasharray="8 6"/>
    <circle r="82" fill="url(#ringRed)"/>
    <circle r="47" fill="#fff"/>
    <rect class="icon" x="-16" y="-26" width="34" height="50" rx="3"/>
    <line class="icon" x1="-6" y1="-14" x2="10" y2="-14"/><line class="icon" x1="-4" y1="-6" x2="10" y2="-6"/><line class="icon" x1="-4" y1="2" x2="10" y2="2"/><line class="icon" x1="-6" y1="12" x2="10" y2="12"/>
    <circle class="icon" cx="-18" cy="-6" r="12" fill="#fff"/>
    <line class="icon" x1="-14" y1="5" x2="-10" y2="20"/>
    <line class="icon" x1="26" y1="-20" x2="26" y2="22"/>
  </g>
  <text class="stage-title" x="1220" y="534">INTERPRET</text>
  <text class="stage-text"><tspan x="1220" y="571">The Analyst;</tspan><tspan x="1220" y="601">business</tspan><tspan x="1220" y="631">intelligence (Bi)</tspan></text>

  <!-- stage: influence -->
  <g class="stage stage-influence" transform="translate(383 787)">
    <circle r="95" fill="none" stroke="var(--green)" stroke-width="2.5" stroke-dasharray="8 6"/>
    <circle r="82" fill="url(#ringGreen)"/>
    <circle r="47" fill="#fff"/>
    <circle class="icon" cx="0" cy="-8" r="9"/>
    <path class="icon" d="M-16 16 Q-16 2 0 2 Q16 2 16 16Z"/>
    <line class="icon" x1="-8" y1="-14" x2="-22" y2="-24"/><circle class="icon" cx="-25" cy="-26" r="3"/>
    <line class="icon" x1="9" y1="-12" x2="24" y2="-24"/><circle class="icon" cx="27" cy="-27" r="3"/>
    <line class="icon" x1="-14" y1="8" x2="-26" y2="6"/><circle class="icon" cx="-29" cy="6" r="3"/>
    <line class="icon" x1="12" y1="10" x2="24" y2="28"/><circle class="icon" cx="26" cy="31" r="3"/>
  </g>
  <text class="stage-title" x="263" y="769" text-anchor="end">INFLUENCE</text>
  <text class="stage-text" text-anchor="end"><tspan x="263" y="806">The Customer</tspan><tspan x="263" y="835">Owner; ignite,</tspan><tspan x="263" y="865">inspire, incite and</tspan><tspan x="263" y="894">promote</tspan></text>

  <!-- stage: innovate -->
  <g class="stage stage-innovate" transform="translate(1073 787)">
    <circle r="95" fill="none" stroke="var(--green)" stroke-width="2.5" stroke-dasharray="8 6"/>
    <circle r="82" fill="url(#ringGreen)"/>
    <circle r="47" fill="#fff"/>
    <path class="icon" d="M-7 12 Q-7 2 -13 -4 A 15 15 0 1 1 13 -4 Q7 2 7 12Z"/>
    <line class="icon" x1="-7" y1="18" x2="7" y2="18"/><line class="icon" x1="-6" y1="24" x2="6" y2="24"/>
    <line class="icon" x1="0" y1="-34" x2="0" y2="-29"/><line class="icon" x1="-24" y1="-22" x2="-20" y2="-18"/><line class="icon" x1="24" y1="-22" x2="20" y2="-18"/>
    <line class="icon" x1="-31" y1="-6" x2="-25" y2="-6"/><line class="icon" x1="31" y1="-6" x2="25" y2="-6"/>
  </g>
  <text class="stage-title" x="1190" y="769">INNOVATE</text>
  <text class="stage-text"><tspan x="1190" y="806">The Planner;</tspan><tspan x="1190" y="835">roadmap and</tspan><tspan x="1190" y="865">lifecycle</tspan><tspan x="1190" y="894">management</tspan></text>

  <!-- stage: implement -->
  <g class="stage stage-implement" transform="translate(523 953)">
    <circle r="95" fill="none" stroke="var(--grey)" stroke-width="2.5" stroke-dasharray="8 6"/>
    <circle r="82" fill="url(#ringGrey)"/>
    <circle r="47" fill="#fff"/>
    <path class="icon" d="M-24 -26 H6 L14 -18 V4 M-24 -26 V26 H0"/>
    <line class="icon" x1="-16" y1="-14" x2="6" y2="-14"/><line class="icon" x1="-16" y1="-5" x2="6" y2="-5"/><line class="icon" x1="-16" y1="4" x2="-2" y2="4"/><line class="icon" x1="-16" y1="13" x2="-4" y2="13"/>
    <circle class="icon" cx="14" cy="16" r="12" stroke-dasharray="4 3" stroke-width="5"/>
    <circle class="icon" cx="14" cy="16" r="5"/>
  </g>
  <text class="stage-title" x="412" y="1011" text-anchor="end">IMPLEMENT</text>
  <text class="stage-text" text-anchor="end"><tspan x="412" y="1048">The Enabler; agile</tspan><tspan x="412" y="1077">systems, platforms</tspan><tspan x="412" y="1107">and channels</tspan></text>

  <!-- stage: identify -->
  <g class="stage stage-identify" transform="translate(928 953)">
    <circle r="95" fill="none" stroke="var(--yellow)" stroke-width="2.5" stroke-dasharray="8 6"/>
    <circle r="82" fill="url(#ringYellow)"/>
    <circle r="47" fill="#fff"/>
    <circle class="icon" cx="-6" cy="-6" r="17"/>
    <path class="icon" d="M-16 -8 A 10 10 0 0 1 -8 -16"/>
    <line class="icon" x1="7" y1="7" x2="26" y2="26" stroke-width="6"/>
  </g>
  <text class="stage-title" x="1045" y="1011">IDENTIFY</text>
  <text class="stage-text"><tspan x="1045" y="1048">The Story teller;</tspan><tspan x="1045" y="1077">individuate</tspan><tspan x="1045" y="1107">innermost value</tspan></text>

  <!-- stage: invest -->
  <g class="stage stage-invest" transform="translate(728 1019)">
    <circle r="95" fill="none" stroke="var(--blue)" stroke-width="2.5" stroke-dasharray="8 6"/>
    <circle r="82" fill="url(#ringBlue)"/>
    <circle r="47" fill="#fff"/>
    <rect class="icon" x="-36" y="-12" width="8" height="24"/>
    <path class="icon" d="M-28 -8 H-6 Q2 -8 4 -2 H-12 M-28 10 H6 L18 2"/>
    <circle class="icon" cx="22" cy="4" r="13"/>
    <text x="22" y="11" text-anchor="middle" class="icon-fill" font-family="Montserrat, sans-serif" font-weight="800" font-size="19">$</text>
  </g>
  <text class="stage-title" x="728" y="1167" text-anchor="middle">INVEST</text>
  <text class="stage-text" text-anchor="middle"><tspan x="728" y="1205">The Catalyst; more value, less</tspan><tspan x="728" y="1234">cost of ownership</tspan></text>
</svg>
</div>
</body>
</html>
```